418 5 minute epoxy adhesive

Hi, i need a label for the front and pack of our New Product.
Just our Vellarn Resins Logo on the front and product name. ( as above)
and Vellarn Fibreglass Logo on the back with mixing instructions on the back.

```html
<!DOCTYPE html>
<html lang="en">
<head>
<meta charset="utf-8">
<title>Vellarn 418 Series – Labels</title>
<link rel="stylesheet" href="https://fonts.googleapis.com/css2?family=Barlow+Condensed:ital,wght@0,800;1,700;1,800&family=Rubik:ital,wght@0,700;0,900;1,700;1,800&family=Rajdhani:wght@400;500;700&display=swap">
<style>
  :root {
    --bg: #3c3c3c;
    --paper: #ffffff;
    --wave: #eceef3;
    --blue: #0d4f9e;
    --blue-dark: #083a78;
    --navy: #3b3f90;
    --red: #e8262f;
    --ink: #161616;
    --body: #2f2f2f;
    --caption: #d9d9d9;
  }
  * { margin: 0; padding: 0; box-sizing: border-box; }
  html, body { width: 1006px; height: 1200px; overflow: hidden; }
  body { background: var(--bg); position: relative; font-family: "Rajdhani", sans-serif; }

  .label { position: absolute; background: var(--paper); }
  .label::before {
    content: ""; position: absolute; inset: 0;
    background: linear-gradient(160deg, var(--wave) 0%, #fff 35%, #fff 70%, #e9f0f8 100%);
  }
  .label__frame {
    position: absolute; inset: 6px;
    border: 4px solid var(--blue); border-radius: 14px;
  }
  .label__frame::after {
    content: ""; position: absolute; inset: 3px;
    border: 1.5px solid var(--red); border-radius: 10px;
  }

  /* Front label */
  .label--front { left: 74px; top: 400px; width: 446px; height: 357px; }
  .brand { position: absolute; display: flex; align-items: center; gap: 10px; }
  .brand__dot { width: 30px; height: 30px; border-radius: 50%; background: var(--red); flex: none; }
  .brand__name { font-family: "Rubik", sans-serif; font-weight: 900; color: var(--blue); white-space: nowrap; }
  .label--front .brand { left: 0; right: 0; top: 50px; justify-content: center; }
  .label--front .brand__name { font-size: 36px; letter-spacing: 0.5px; }
  .tagline {
    position: absolute; left: 0; right: 0; top: 98px; text-align: center;
    font-family: "Rubik", sans-serif; font-weight: 700; font-size: 12px;
    letter-spacing: 1.6px; color: var(--blue);
  }
  .series-hero {
    position: absolute; left: 0; right: 0; top: 122px; text-align: center;
    font-family: "Barlow Condensed", sans-serif; font-weight: 800; font-size: 86px; line-height: 1;
    background: linear-gradient(180deg, var(--blue) 0%, #1b6cc4 45%, var(--blue-dark) 100%);
    -webkit-background-clip: text; background-clip: text; color: transparent;
  }
  .rule-red { position: absolute; left: 56px; right: 56px; top: 220px; height: 3px; background: var(--red); }
  .cure-tag {
    position: absolute; left: 108px; width: 230px; top: 224px; height: 34px;
    background: var(--red); clip-path: polygon(0 0, 100% 0, 92% 100%, 8% 100%);
    color: #fff; text-align: center;
    font-family: "Rubik", sans-serif; font-style: italic; font-weight: 800; font-size: 31px; line-height: 34px;
  }
  .product-type {
    position: absolute; left: 0; right: 0; top: 258px; text-align: center;
    font-family: "Rubik", sans-serif; font-style: italic; font-weight: 800; font-size: 33px;
    letter-spacing: -1px; color: var(--ink);
  }
  .volume-tab {
    position: absolute; left: 124px; width: 198px; top: 314px; height: 33px;
    background: var(--blue); clip-path: polygon(9% 0, 91% 0, 100% 100%, 0 100%);
    color: #fff; text-align: center;
    font-family: "Barlow Condensed", sans-serif; font-style: italic; font-weight: 800; font-size: 26px; line-height: 34px;
  }
  .caution { position: absolute; left: 337px; top: 333px; font-size: 6px; color: var(--ink); font-weight: 500; }

  /* Back label */
  .label--back { left: 585px; top: 398px; width: 360px; height: 360px; }
  .label--back .brand { left: 0; right: 0; top: 52px; justify-content: center; gap: 8px; }
  .label--back .brand__dot { width: 22px; height: 22px; background: var(--navy); }
  .label--back .brand__name { font-size: 22px; color: var(--red); }
  .series-title {
    position: absolute; left: 0; right: 0; top: 110px; text-align: center;
    font-family: "Rubik", sans-serif; font-weight: 900; font-size: 31px; color: var(--navy);
  }
  .type-band {
    position: absolute; left: 14px; right: 14px; top: 149px; height: 28px;
    background: var(--red); color: #fff; text-align: center;
    font-family: "Rubik", sans-serif; font-style: italic; font-weight: 800; font-size: 20px; line-height: 28px;
  }
  .description {
    position: absolute; left: 34px; right: 34px; top: 182px;
    font-size: 10.6px; line-height: 13px; color: var(--body); text-align: justify; text-align-last: center;
  }
  .description strong { font-weight: 700; color: var(--ink); }
  .mix-ratio {
    position: absolute; left: 0; right: 0; top: 317px; text-align: center;
    font-size: 12px; font-weight: 700; color: var(--navy);
  }

  .size-note {
    position: absolute; top: 808px; font-family: "Rajdhani", sans-serif; font-weight: 400;
    font-size: 15px; letter-spacing: 1px; color: var(--caption);
  }
  .size-note--front { left: 80px; }
  .size-note--back { left: 585px; }
</style>
</head>
<body>

<section class="label label--front" aria-label="Front label">
  <div class="label__frame"></div>
  <div class="brand"><span class="brand__dot"></span><span class="brand__name">VELLARN RESINS</span></div>
  <p class="tagline">BUILT FOR PERFORMANCE</p>
  <h1 class="series-hero">418 SERIES</h1>
  <div class="rule-red"></div>
  <div class="cure-tag">5 MINUTE</div>
  <p class="product-type">EPOXY ADHESIVE</p>
  <div class="volume-tab">200 MLS KIT</div>
  <p class="caution">Read Cautions on the back panel</p>
</section>

<section class="label label--back" aria-label="Back label">
  <div class="label__frame"></div>
  <div class="brand"><span class="brand__dot"></span><span class="brand__name">VELLARN FIBREGLASS</span></div>
  <h2 class="series-title">418 SERIES</h2>
  <div class="type-band">5 MINUTE EPOXY ADHESIVE</div>
  <p class="description"><strong>418 Series</strong> is a two part, free flowing liquid epoxy that sets in just 5 minutes. It bonds a broad range of materials with strong adhesion and lasting strength, making it the go-to adhesive for everyday repairs and general purpose jobs. It mixes at a simple 1:1 ratio, and fillers can be added to build a thicker glue paste for gaps and vertical work. With a very long shelf life, 418 Series is the one glue every workshop and shed should keep on hand. Reach for Vellarn 418 Series for great value and dependable results.</p>
  <p class="mix-ratio">Mix at a ratio of 1 Part A : 1 Part B (418A : 418B)</p>
</section>

<p class="size-note size-note--front">100MM X 80MM</p>
<p class="size-note size-note--back">100MM X 100MM</p>

</body>
</html>
```